Business Card for a New Zealand IT Startup

I need a business card for VELTA Holdings. We are a young startup based in New Zealand working in internet marketing and web development. The design should have some element connected to New Zealand, such as wave, koru or silver fern, just don't use a kiwi bird.

```html
<!DOCTYPE html>
<html lang="en">
<head>
<meta charset="utf-8">
<title>VELTA Holdings – Business Card</title>
<link rel="stylesheet" href="https://fonts.googleapis.com/css2?family=Roboto:wght@400;500;700&display=swap">
<style>
  :root {
    --bg: #2a2a2a;
    --card-white: #ffffff;
    --brand-blue: #0a6fbb;
    --brand-orange: #f26126;
    --text-grey: #5a5a5a;
    --divider: #c9c9c9;
  }
  * { margin: 0; padding: 0; box-sizing: border-box; }
  html, body {
    width: 1125px; height: 1200px; overflow: hidden;
    background: var(--bg);
    font-family: "Roboto", Arial, sans-serif;
  }
  .canvas { position: relative; width: 1125px; height: 1200px; }

  .card {
    position: absolute; left: 150px; width: 825px; height: 470px;
    border-radius: 22px; overflow: hidden;
  }
  .card--front { top: 98px; background: var(--card-white); }
  .card--back { top: 631px; background: var(--brand-blue); }

  .brand-name {
    position: absolute; left: 70px; top: 192px; width: 350px;
    text-align: center;
    font-size: 44px; font-weight: 700; color: var(--brand-blue);
    line-height: 60px; letter-spacing: 1px;
  }

  .divider {
    position: absolute; left: 455px; top: 72px; width: 2px; height: 300px;
    background: linear-gradient(to bottom, transparent, var(--divider) 15%, var(--divider) 85%, transparent);
  }

  .contact { position: absolute; left: 492px; top: 86px; color: var(--text-grey); }
  .contact__name {
    font-size: 29px; font-weight: 500; color: var(--brand-blue); line-height: 34px;
  }
  .contact__title {
    font-size: 21px; color: var(--brand-orange); line-height: 26px; margin-bottom: 12px;
  }
  .contact__address { font-size: 19.5px; line-height: 24.5px; margin-bottom: 14px; }
  .contact__list { list-style: none; }
  .contact__item {
    display: flex; align-items: center; gap: 12px;
    font-size: 19.5px; line-height: 26.3px;
  }
  .contact__icon { width: 19px; height: 19px; flex: none; fill: var(--brand-blue); }

  .card__band { position: absolute; left: 0; bottom: 0; width: 825px; height: 19px; }

  .back-dot {
    position: absolute; left: 352px; top: 78px; width: 120px; height: 120px;
    border-radius: 50%; background: var(--card-white);
  }
  .back-name {
    position: absolute; left: 0; width: 100%; top: 222px;
    text-align: center; color: var(--card-white);
    font-size: 44px; font-weight: 700; line-height: 56px; letter-spacing: 1px;
  }
  .back-wave {
    position: absolute; left: 262px; top: 300px; width: 300px; height: 24px;
  }
  .back-web {
    position: absolute; left: 0; width: 100%; top: 390px;
    text-align: center; color: var(--card-white);
    font-size: 19px; letter-spacing: 6.5px;
  }
</style>
</head>
<body>
<main class="canvas">
  <section class="card card--front" aria-label="Business card front">
    <div class="brand-name">VELTA Holdings</div>
    <div class="divider"></div>
    <div class="contact">
      <div class="contact__name">MARA TANE</div>
      <div class="contact__title">CEO/FOUNDER</div>
      <div class="contact__address">142 Harbour Crescent<br>Wellington, NZ 6011</div>
      <ul class="contact__list">
        <li class="contact__item">
          <svg class="contact__icon" viewBox="0 0 24 24"><path d="M6.6 10.8a15.1 15.1 0 0 0 6.6 6.6l2.2-2.2c.3-.3.7-.4 1-.2 1.1.4 2.3.6 3.6.6.6 0 1 .4 1 1V20c0 .6-.4 1-1 1A17 17 0 0 1 3 4c0-.6.4-1 1-1h3.5c.6 0 1 .4 1 1 0 1.3.2 2.5.6 3.6.1.3 0 .7-.2 1z"/></svg>
          604 218 3375
        </li>
        <li class="contact__item">
          <svg class="contact__icon" viewBox="0 0 24 24"><path d="M7 1h10a2 2 0 0 1 2 2v18a2 2 0 0 1-2 2H7a2 2 0 0 1-2-2V3a2 2 0 0 1 2-2zm0 3v14h10V4zm5 15.5a1.2 1.2 0 1 0 0 2.4 1.2 1.2 0 0 0 0-2.4z"/></svg>
          021 557 4182
        </li>
        <li class="contact__item">
          <svg class="contact__icon" viewBox="0 0 24 24"><path d="M6 2h10v6H6zM2 10h20v8h-4v-3H6v3H2zm5 6h10v6H7z"/></svg>
          604 218 3390
        </li>
        <li class="contact__item">
          <svg class="contact__icon" viewBox="0 0 24 24"><path d="M2 5h20v14H2zm2 2v.5l8 5 8-5V7zm0 2.8V17h16V9.8l-8 5z"/></svg>
          mara@veltaholdings.com
        </li>
        <li class="contact__item">
          <svg class="contact__icon" viewBox="0 0 24 24"><circle cx="12" cy="12" r="10"/><path d="M8 6c2 1 1 3 3 3s1 3-1 4-1 4-3 3M14 15c1-1 3-1 4 1" stroke="#fff" stroke-width="1.6" fill="none"/></svg>
          www.veltaholdings.com
        </li>
      </ul>
    </div>
    <svg class="card__band" viewBox="0 0 825 19" preserveAspectRatio="none" aria-hidden="true">
      <polygon points="0,0 559,0 553,19 0,19" fill="var(--brand-blue)"/>
      <polygon points="565,0 825,0 825,19 559,19" fill="var(--brand-orange)"/>
    </svg>
  </section>

  <section class="card card--back" aria-label="Business card back">
    <div class="back-dot"></div>
    <div class="back-name">VELTA Holdings</div>
    <svg class="back-wave" viewBox="0 0 300 24" aria-hidden="true">
      <path d="M2 12 Q27 0 52 12 T102 12 T152 12 T202 12 T252 12 T298 12" fill="none" stroke="var(--card-white)" stroke-width="3" stroke-linecap="round"/>
    </svg>
    <div class="back-web">www.veltaholdings.com</div>
  </section>
</main>
</body>
</html>
```